Kelvaro.ch is looking for business card letterhead and envelope C5 with WOW effect

We need a strong business card for our company Kelvaro.ch, logo is available. You want a black or dark background on which the logo Stark r% 26 # 252; appears. Letterhead and envelope in C5 format should be in a similar design, but does not have to be We need a strong business card for our company Kelvaro.ch, logo is available. A black or dark background is desired, on which the logo Stark comes across. The letterhead and the envelope in C5 format should have a similar design.

Target Market(s)

Private customers as well as entrepreneurs

Contact Information for Business Card

E-mail: info@kelvaro-example.ch
Web.www.Kelvaro-example.ch
Tel: +41 ( 0 ) 79 482 6037
Adresse:
Lindenweg 14
9406 Tarnbach

Hier kann man Icons verwenden für Email,Tel und Adressse

Font styles to use
Other font styles liked:
• Dubai,bold

Colors

Designer to choose colors to be used in the design.

Requirements
Must have
• WOW effect
Nice to have
• R% 26 # 252; back business card with our service listings. - VEHICLE LABELING - SHOP WINDOW LABELING - STICKERS AND MUCH MORE ... in red color

```html
<!DOCTYPE html>
<html lang="en">
<head>
<meta charset="utf-8">
<title>Kelvaro.ch – Business Card</title>
<link rel="stylesheet" href="https://fonts.googleapis.com/css2?family=Montserrat:wght@400;500;700&display=swap">
<style>
  :root {
    --bg: #2a2a2c;
    --card: #1d1d1e;
    --yellow: #fcc419;
    --yellow-deep: #f0b60f;
    --white: #f2f2f2;
    --rule: #5a5a5a;
  }
  * { margin: 0; padding: 0; box-sizing: border-box; }
  html, body { width: 1200px; height: 913px; overflow: hidden; }
  body {
    background: var(--bg);
    font-family: "Montserrat", sans-serif;
    position: relative;
  }
  .card {
    position: absolute;
    width: 560px;
    height: 320px;
    background: var(--card);
    box-shadow: 0 12px 30px rgba(0,0,0,.45);
    overflow: hidden;
  }
  /* Front */
  .card-front { left: 80px; top: 110px; }
  .brand {
    position: absolute;
    left: 0; right: 0; top: 118px;
    display: flex; align-items: center; justify-content: center; gap: 14px;
  }
  .brand-mark { width: 22px; height: 22px; background: var(--yellow); }
  .brand-name {
    color: var(--white);
    font-weight: 700;
    font-size: 36px;
    letter-spacing: 1px;
    text-transform: uppercase;
  }
  .services {
    position: absolute;
    left: 0; right: 0; bottom: 58px;
    text-align: center;
    color: var(--white);
    font-size: 14px;
    font-weight: 500;
    letter-spacing: .3px;
  }
  .services .dot {
    display: inline-block; width: 7px; height: 7px; border-radius: 50%;
    background: var(--yellow); margin: 0 8px; vertical-align: middle;
  }
  /* Back */
  .card-back { left: 560px; top: 480px; }
  .decor-area {
    position: absolute;
    right: 0; top: 0;
    width: 310px; height: 180px;
    background: linear-gradient(135deg, var(--yellow) 0%, var(--yellow-deep) 100%);
  }
  .divider {
    position: absolute;
    left: 28px; right: 28px; top: 196px;
    height: 1px; background: var(--rule);
  }
  .person { position: absolute; left: 28px; top: 208px; }
  .person-name { color: var(--yellow); font-weight: 700; font-size: 20px; }
  .person-role { color: var(--white); font-size: 13px; font-weight: 500; margin-top: 2px; }
  .contacts {
    position: absolute; left: 28px; right: 20px; top: 262px;
    display: grid; grid-template-columns: auto auto; gap: 6px 22px;
    color: var(--white); font-size: 12px; list-style: none;
  }
  .contacts li { display: flex; align-items: center; gap: 8px; white-space: nowrap; }
  .contacts svg { width: 12px; height: 12px; fill: var(--yellow); flex: none; }
</style>
</head>
<body>
  <section class="card card-front">
    <div class="brand">
      <span class="brand-mark"></span>
      <span class="brand-name">Kelvaro.ch</span>
    </div>
    <p class="services">Vehicle Labeling<span class="dot"></span>Shop Window Labeling<span class="dot"></span>Stickers</p>
  </section>

  <section class="card card-back">
    <div class="decor-area" role="img" aria-label="Brand decoration area in yellow"></div>
    <div class="divider"></div>
    <div class="person">
      <p class="person-name">Jonas Brunner</p>
      <p class="person-role">President</p>
    </div>
    <ul class="contacts">
      <li>
        <svg viewBox="0 0 24 24"><path d="M6.6 10.8a15.1 15.1 0 0 0 6.6 6.6l2.2-2.2a1 1 0 0 1 1-.25 11.4 11.4 0 0 0 3.6.57 1 1 0 0 1 1 1V20a1 1 0 0 1-1 1A17 17 0 0 1 3 4a1 1 0 0 1 1-1h3.5a1 1 0 0 1 1 1 11.4 11.4 0 0 0 .57 3.6 1 1 0 0 1-.25 1z"/></svg>
        +41 ( 0 ) 79 482 6037
      </li>
      <li>
        <svg viewBox="0 0 24 24"><path d="M12 2a10 10 0 1 0 0 20 10 10 0 0 0 0-20zm0 2c1 1.2 1.8 3 2.1 5H9.9C10.2 7 11 5.2 12 4zM4.3 13h3.6a16 16 0 0 0 .4 4.3A8 8 0 0 1 4.3 13zm0-2a8 8 0 0 1 4-4.3A16 16 0 0 0 7.9 11zm7.7 9c-1-1.2-1.8-3-2.1-5h4.2c-.3 2-1.1 3.8-2.1 5zm2.3-11H9.7a16 16 0 0 0 0 4h4.6a16 16 0 0 0 0-4zm1.4 8.3a16 16 0 0 0 .4-4.3h3.6a8 8 0 0 1-4 4.3zM16.1 11a16 16 0 0 0-.4-4.3 8 8 0 0 1 4 4.3z"/></svg>
        www.Kelvaro-example.ch
      </li>
      <li>
        <svg viewBox="0 0 24 24"><path d="M12 2a7 7 0 0 0-7 7c0 5 7 13 7 13s7-8 7-13a7 7 0 0 0-7-7zm0 9.5A2.5 2.5 0 1 1 12 6.5a2.5 2.5 0 0 1 0 5z"/></svg>
        Lindenweg 14 9406 Tarnbach
      </li>
      <li>
        <svg viewBox="0 0 24 24"><path d="M2 5h20v14H2zm2 2v.4l8 5 8-5V7zm0 2.8V17h16V9.8l-8 5z"/></svg>
        info@kelvaro-example.ch
      </li>
    </ul>
  </section>
</body>
</html>
```